Bespoke Builders Business Card Design

We need a business card for an established builder of high quality bespoke homes in Auckland and Northland. We build and renovate homes collaboratively facilitating effective communication between owners, builders, architects, suppliers and tradespeople. We have never built or renovated a home that leaks or has faults. We only use reliable materials. We have never been sued or had legal action taken against us. We are honest builders of bespoke homes not group mass produced homes. Our niche market is in character homes. We practice sustainability and have built a lot of coastal property. We have been in business for over thirty years . We would like to see natural colors of the environment sand,sea and maybe vegetation . The design should communicate quality, sustainability,fair pricing, open communication and the originality of bespoke building. And the fact that the builder is registered.

Industry/Entity Type

Business

Contact Information for Business Card

Rowan Tellick Builders
Ph. 021583917
18 Kestrel Rd Harwood Bay Auckland 0814
PO Box 927 Kaiwhenua 0583

```html
<!DOCTYPE html>
<html lang="en">
<head>
<meta charset="utf-8">
<title>Rowan Tellick Builders – Business Card</title>
<link rel="stylesheet" href="https://fonts.googleapis.com/css2?family=Crimson+Text:wght@400&family=Open+Sans:wght@400&display=swap">
<style>
  :root {
    --bg: #e9e6e1;
    --card: #f4f4f4;
    --ink: #1c1c1c;
    --rule: #2a2a2a;
    --navy: #0b3476;
    --wave-grey: #b9b9b9;
    --contact: #eef2fa;
    --house-a: #d9d4cc;
    --house-b: #efece8;
  }
  * { box-sizing: border-box; margin: 0; padding: 0; }
  html, body { width: 1200px; height: 902px; overflow: hidden; }
  body {
    background: var(--bg);
    display: flex;
    flex-direction: column;
    align-items: center;
    justify-content: center;
    gap: 20px;
  }
  .card {
    position: relative;
    width: 740px;
    height: 423px;
    background: var(--card);
    overflow: hidden;
    box-shadow: 0 2px 8px rgba(0,0,0,0.12);
  }
  .brand-name {
    font-family: "Crimson Text", Georgia, serif;
    font-weight: 400;
    color: var(--ink);
    white-space: nowrap;
  }
  /* Front */
  .card-front .house-image {
    position: absolute;
    left: 250px;
    top: 110px;
    width: 260px;
    height: 220px;
    background: radial-gradient(ellipse at 50% 45%, var(--house-a) 0%, var(--house-b) 60%, var(--card) 100%);
    opacity: 0.85;
  }
  .card-front .brand-name {
    position: absolute;
    left: 0; right: 0;
    top: 165px;
    text-align: center;
    font-size: 70px;
    letter-spacing: 1px;
  }
  /* Back */
  .card-back .wave {
    position: absolute;
    inset: 0;
    width: 100%;
    height: 100%;
  }
  .card-back .title-row {
    position: absolute;
    left: 0; right: 0;
    top: 92px;
    display: flex;
    align-items: center;
    gap: 12px;
  }
  .card-back .title-row .rule {
    flex: 1;
    height: 2px;
    background: var(--rule);
  }
  .card-back .brand-name { font-size: 50px; }
  .contact {
    position: absolute;
    left: 260px; right: 0;
    top: 292px;
    text-align: center;
    font-family: "Open Sans", Arial, sans-serif;
    font-size: 20px;
    line-height: 1.3;
    color: var(--contact);
    list-style: none;
  }
</style>
</head>
<body>
  <section class="card card-front" aria-label="Business card front">
    <div class="house-image" role="img" aria-label="Faded illustration of a timber-framed house under construction"></div>
    <h1 class="brand-name">Rowan Tellick Builders</h1>
  </section>

  <section class="card card-back" aria-label="Business card back">
    <svg class="wave" viewBox="0 0 740 423" preserveAspectRatio="none" aria-hidden="true">
      <path d="M0 330 C200 335 330 300 440 240 C540 185 640 160 740 155 L740 423 L0 423 Z" fill="var(--wave-grey)"/>
      <path d="M0 346 C200 351 330 316 440 256 C545 202 645 178 740 174 L740 423 L0 423 Z" fill="var(--navy)"/>
    </svg>
    <div class="title-row">
      <span class="rule"></span>
      <h2 class="brand-name">Rowan Tellick Builders</h2>
      <span class="rule"></span>
    </div>
    <ul class="contact">
      <li>021583917</li>
      <li>18 Kestrel Rd Harwood Bay Auckland 0814</li>
      <li>PO Box 927 Kaiwhenua 0583</li>
    </ul>
  </section>
</body>
</html>
```